Gobal construction supply company needs new business card design

I need a business card design for my global supply company using an existing logo. i will be looking to print these on rounded corner cards with the black background version of my logo on the back. on the front white background, my logo again and my simple details.

```html
<!DOCTYPE html>
<html lang="en">
<head>
<meta charset="UTF-8">
<title>Meridian Building Supply – Business Cards</title>
<link href="https://fonts.googleapis.com/css2?family=Montserrat:wght@400;500;700&display=swap" rel="stylesheet">
<style>
  :root {
    --backdrop: #3a3b3e;
    --card-white: #ffffff;
    --card-black: #141414;
    --ink-dark: #111111;
    --ink-light: #ffffff;
    --accent-red: #e0141b;
    --muted-light: #d8d8d8;
  }
  * { margin: 0; padding: 0; box-sizing: border-box; }
  html, body {
    width: 1200px;
    height: 1000px;
    overflow: hidden;
    background: var(--backdrop);
    font-family: "Montserrat", sans-serif;
  }
  .canvas {
    position: relative;
    width: 1200px;
    height: 1000px;
  }
  .card {
    position: absolute;
    left: 280px;
    width: 640px;
    height: 366px;
    border-radius: 26px;
    display: flex;
    flex-direction: column;
    align-items: center;
    justify-content: center;
    text-align: center;
  }
  .card--front {
    top: 70px;
    background: var(--card-white);
  }
  .card--back {
    top: 520px;
    background: var(--card-black);
    color: var(--ink-light);
    justify-content: flex-start;
    padding-top: 44px;
  }
  .brand {
    display: flex;
    align-items: center;
    gap: 14px;
  }
  .brand__name {
    font-weight: 700;
    font-size: 30px;
    letter-spacing: 0.5px;
    text-transform: uppercase;
  }
  .card--front .brand__name { color: var(--ink-dark); }
  .card--back .brand__name { color: var(--ink-light); font-size: 26px; }
  .brand__dot {
    width: 22px;
    height: 22px;
    border-radius: 50%;
    background: var(--accent-red);
    flex: none;
  }
  .card--back .brand__dot { width: 18px; height: 18px; }
  .holder {
    margin-top: 34px;
  }
  .holder__name {
    color: var(--accent-red);
    font-weight: 700;
    font-size: 22px;
    text-transform: uppercase;
    letter-spacing: 0.5px;
  }
  .holder__title {
    font-size: 15px;
    font-weight: 500;
    color: var(--muted-light);
    margin-top: 2px;
  }
  .divider {
    width: 150px;
    height: 2px;
    background: var(--accent-red);
    margin: 12px auto 14px;
  }
  .contact {
    font-size: 15px;
    font-weight: 500;
    line-height: 1.55;
  }
  .contact__web-domain { color: var(--accent-red); }
</style>
</head>
<body>
  <main class="canvas">
    <section class="card card--front" aria-label="Business card front">
      <div class="brand">
        <span class="brand__name">Meridian Building Supply</span>
        <span class="brand__dot"></span>
      </div>
    </section>

    <section class="card card--back" aria-label="Business card back">
      <div class="brand">
        <span class="brand__name">Meridian Building Supply</span>
        <span class="brand__dot"></span>
      </div>
      <div class="holder">
        <p class="holder__name">Daniel Hartley</p>
        <p class="holder__title">Managing Director</p>
      </div>
      <div class="divider"></div>
      <div class="contact">
        <p>48 Harbour Road, Portside, NSW 2000</p>
        <p>+1 (555) 010 2040 &nbsp;|&nbsp; +1 (555) 010 2040</p>
        <p>dan@meridianbs.com &nbsp;|&nbsp; www.<span class="contact__web-domain">meridianbs</span>.com</p>
      </div>
    </section>
  </main>
</body>
</html>
```